Corvanth Veylor - Advanced Skincare and undetectable Makeup for Men

We are in need of a professional webpage for our company Corvanth Veylor. We help every man feel his best by looking his best. Inspired by the myth of Corvanth, we offer makeup and skincare products along with education upon their use. Our mission is to celebrate masculinity in all of its forms, regardless of age, race, sexual orientation, or assigned gender at birth.

The webpage would serve as our online store, as a place where our clients can learn about our brand, view our "How-to" video tutorials, and get product information. An online blog will also be hosted in order to keep clients up to date with news, updates, media mentions, etc.

The color schemes that we use are mostly Black and Gold, with Red accents. please keep in mind that this is a men's cosmetics line, and therefore should read powerful, sexy, confident and bold - all with a high end look and feel.

Think along the lines of brands like Lem Brisko, QDV, Belluti, etc.

our logo is included in the files attached. images and copy will be added in at a later time; hence, general images that fit the feel and filler text is encouraged.

The products to be sold include:
a face cleanser in a pump dispenser bottle (1 size)
a mask in a round jar container (1 size)
a moisturizer in a pump container 1 size)
a concealer in a click pen with a brush applicator (3 shades)
a liquid liner pen (4 shades)
a contouring palette (2 shade options)
a setting spray (single option)

Target Market(s)

Millennial Men

Industry/Entity Type

Beauty

Number of Pages Required

5+ page

Font styles to use
Serif

Colors
ec1f27
000000
faa54b

Requirements
Must have
• ur essential requirements are:
• 1) a stunning and engaging landing page that truly captures the ideals of sexuality, boldness and confidence.
• 2) an interactive and engaging online store that is easy to update / add product / information to.
• 3) Product pages supporting various toggling images of the product, a shade selection option, ingredient information, usage instructions, pricing, and a link to a "how to video" unique to each individual product.
• 4) dedicated space where all of the tutorials can be organized together
• 5) an organized Blog section, that would include a segment for a Q&A section for us to update as the brand grows, ongoing contests (that would be easily hidden if there are no contests running at the moment) as well as general news and updates segment.
• 6) an "about us" page, where our customers are able to learn about our story, inspirations, humanitarian efforts and philosophies in product contents and purity.
• 7) a contact us page, which would include social media links, contact email and telephone number as well as physical address to be updated upon launch.
• 8) discrete privacy policy, terms of use, and return policy links available at the bottom of every page
Nice to have
• 1) A posting forum where clients could post their looks using our products, or maybe a live stream of our Pictoval account.
• 2) a member sign in page so that we can collect and store customer information for faster check out, keep track of purchases attached to their email address (future loyalty program plans) and maintain an email database for email notifications and the such.

```html
<!DOCTYPE html>
<html lang="en">
<head>
<meta charset="utf-8">
<title>Corvanth Veylor — Skincare and Makeup for Men</title>
<link rel="stylesheet" href="https://fonts.googleapis.com/css2?family=Cinzel:wght@400;700&family=Lato:wght@400;700&display=swap">
<style>
:root{
  --gold:#faa54b;
  --gold-deep:#e8913a;
  --red:#ec1f27;
  --black:#000;
  --ink:#222;
  --muted:#666;
  --line:#dcdcdc;
  --paper:#fff;
  --mist:#f1f1f1;
  --night:#0d1020;
}
*{box-sizing:border-box;margin:0;padding:0}
html,body{width:1200px;height:3220px;overflow:hidden;background:var(--paper)}
body{font-family:"Lato",Arial,sans-serif;color:var(--ink);position:relative}
.serif{font-family:"Cinzel","Times New Roman",serif}

/* top bar */
.topbar{position:absolute;top:0;left:0;width:1200px;height:36px;display:flex;justify-content:space-between;align-items:center;padding:0 16px;font-size:13px;color:var(--ink)}
.topbar .phone{display:flex;align-items:center;gap:6px}
.social{display:flex;gap:10px}
.social span{width:14px;height:14px;border-radius:50%;background:var(--ink)}

/* brand */
.brand{position:absolute;top:36px;left:0;width:1200px;text-align:center}
.brand-mark{display:block;width:44px;height:44px;margin:6px auto 8px;border-radius:50%;background:var(--gold)}
.brand-name{font-family:"Cinzel",serif;font-weight:700;font-size:22px;letter-spacing:3px;color:var(--ink)}

/* nav */
.nav{position:absolute;top:170px;left:0;width:1200px;height:40px;border-top:1px solid var(--line);border-bottom:1px solid var(--line);display:flex;align-items:center;padding:0 70px}
.nav a{font-size:13px;color:var(--ink);text-decoration:none;margin-right:30px;text-transform:uppercase}
.nav a.active{color:var(--gold)}
.nav .tools{margin-left:auto;display:flex;gap:22px;align-items:center}

/* hero */
.hero{position:absolute;top:220px;left:0;width:1200px;height:550px;background:radial-gradient(circle at 40% 40%,#2c3550 0%,#10142a 55%,#05060d 100%)}
.hero-visual{position:absolute;right:0;top:0;width:620px;height:550px;background:linear-gradient(90deg,rgba(0,0,0,0) 0%,#5b6a86 45%,#c9c6c6 75%,#e8e3df 100%)}
.hero-title{position:absolute;left:78px;top:178px;font-family:"Cinzel",serif;font-weight:700;font-size:44px;color:var(--gold);letter-spacing:1px}
.hero-text{position:absolute;left:78px;top:262px;width:400px;font-size:16px;line-height:1.55;color:#fff}

/* new products */
.deco{position:absolute;border-radius:20px;opacity:.55}
.deco.left{left:30px;top:840px;width:180px;height:260px;background:linear-gradient(160deg,#cfe9e0,#b5cde8)}
.deco.right{right:30px;top:1180px;width:200px;height:170px;background:linear-gradient(200deg,#c7d6f2,#b9c3ef)}
.section-title{font-family:"Cinzel",serif;font-size:32px;color:var(--gold);text-align:center;letter-spacing:1px}
.products-title{position:absolute;top:868px;left:0;width:1200px}
.products{position:absolute;top:944px;left:80px;display:flex;gap:44px}
.card{width:236px;height:306px;background:var(--paper);border:1px solid var(--line);box-shadow:0 4px 12px rgba(0,0,0,.12);text-align:center}
.card .shot{margin:14px auto 0;width:206px;height:200px;background:linear-gradient(180deg,#fff 0%,#f3f3f3 100%);display:flex;justify-content:center;align-items:center}
.card .shot i{display:block;width:40px;height:120px;border-radius:6px;background:linear-gradient(90deg,#111,#3a3a3a,#111)}
.card .name{margin-top:34px;font-size:15px;text-transform:uppercase;color:var(--ink)}

/* range */
.range{position:absolute;top:1390px;left:0;width:1200px;height:500px;background:linear-gradient(90deg,#f6f6f6 0%,#ececec 60%,#e5e5e5 100%)}
.range-visual{position:absolute;right:0;top:0;width:520px;height:500px;background:linear-gradient(90deg,rgba(236,236,236,0) 0%,#d9c3b2 45%,#b89580 75%,#6d5a52 100%)}
.diamond{position:absolute;width:112px;height:112px;transform:rotate(45deg);background:var(--paper);border:2px solid #f4c9a0;box-shadow:0 3px 8px rgba(0,0,0,.08)}
.diamond.featured{width:140px;height:140px;background:#fbd9b4;border-color:var(--gold)}
.diamond .inner{position:absolute;inset:0;transform:rotate(-45deg);display:flex;align-items:center;justify-content:center;gap:8px}
.diamond .item{width:22px;height:46px;border-radius:4px;background:linear-gradient(180deg,#b5272d,#5a1216)}
.diamond .label{font-size:11px;color:var(--red);width:58px;line-height:1.2}
.diamond.featured .label{color:var(--ink);font-size:13px}

/* faq */
.faq-visual{position:absolute;top:2040px;left:130px;width:180px;height:420px;background:linear-gradient(135deg,#f2f2f2 0%,#2a2a2a 50%,#f2f2f2 52%,#fff 100%)}
.faq{position:absolute;top:2060px;left:520px;width:570px}
.faq h2{font-family:"Cinzel",serif;font-size:34px;color:var(--gold);margin-bottom:28px;margin-left:4px}
.faq-item{border-bottom:1px solid var(--line);padding:10px 0;display:flex;gap:14px;font-size:14px;color:var(--ink)}
.faq-item svg{flex:none;margin-top:1px}
.faq-item p.answer{font-size:12px;color:var(--muted);line-height:1.5;margin-top:10px}

/* blog */
.blog{position:absolute;top:2530px;left:0;width:1200px;height:570px;background:radial-gradient(circle at 15% 20%,#6a4a1e 0%,rgba(0,0,0,0) 22%),radial-gradient(circle at 70% 25%,#4d3a1c 0%,rgba(0,0,0,0) 20%),radial-gradient(circle at 40% 90%,#3d2e17 0%,rgba(0,0,0,0) 25%),#0a0806}
.blog-title{position:absolute;top:82px;left:0;width:1200px}
.posts{position:absolute;top:130px;left:80px;display:flex;gap:32px}
.post{width:320px;height:410px;border:1px solid #6b6b6b;position:relative;background:rgba(20,20,20,.6)}
.post .photo{height:200px;background:linear-gradient(160deg,#7fa8c8 0%,#c9a083 55%,#5c4638 100%)}
.post .avatar{position:absolute;right:16px;top:176px;width:48px;height:48px;border-radius:50%;background:#c9a083;border:3px solid #fff}
.post .body{padding:40px 18px 0;color:#fff}
.post h3{font-size:17px;font-weight:700;margin-bottom:8px}
.post p{font-size:13px;line-height:1.5;color:#ddd}
.post .more{display:inline-block;margin-top:10px;font-size:12px;color:#fff;text-decoration:underline}

/* footer */
.footer{position:absolute;top:3100px;left:0;width:1200px;height:120px;background:var(--black);color:#ccc;font-size:13px;display:flex;justify-content:center;align-items:center}
</style>
</head>
<body>

<header>
  <div class="topbar">
    <div class="phone">
      <svg width="14" height="14" viewBox="0 0 24 24"><path fill="#222" d="M6.6 10.8a15 15 0 0 0 6.6 6.6l2.2-2.2c.3-.3.7-.4 1-.2 1.1.4 2.3.6 3.6.6.6 0 1 .4 1 1V20c0 .6-.4 1-1 1A17 17 0 0 1 3 4c0-.6.4-1 1-1h3.5c.6 0 1 .4 1 1 0 1.3.2 2.5.6 3.6.1.3 0 .7-.2 1z"/></svg>
      <span>123 456 7890</span>
    </div>
    <div class="social" aria-label="Social links"><span></span><span></span><span></span></div>
  </div>

  <div class="brand">
    <span class="brand-mark"></span>
    <div class="brand-name">CORVANTH VEYLOR</div>
  </div>

  <nav class="nav">
    <a class="active" href="#">Home</a>
    <a href="#">About</a>
    <a href="#">Products</a>
    <a href="#">FAQ</a>
    <a href="#">Blog</a>
    <a href="#">Contact Us</a>
    <div class="tools">
      <svg width="18" height="18" viewBox="0 0 24 24" fill="none" stroke="#222" stroke-width="2.4"><circle cx="10" cy="10" r="7"/><path d="M15 15l6 6"/></svg>
      <svg width="20" height="20" viewBox="0 0 24 24" fill="none" stroke="#222" stroke-width="2"><path d="M3 5h3l2.5 10h10L21 8H7"/><circle cx="10" cy="19" r="1.5"/><circle cx="17" cy="19" r="1.5"/></svg>
    </div>
  </nav>
</header>

<section class="hero">
  <div class="hero-visual" role="img" aria-label="Well-groomed man beside bottles of setting spray and cologne"></div>
  <h1 class="hero-title">CORVANTH VEYLOR</h1>
  <p class="hero-text">Lorem Ipsum is simply dummy text of the printing and typesetting industry. Lorem Ipsum has been the industry's standard dummy text ever since the 1500s.</p>
</section>

<div class="deco left" role="img" aria-label="Watercolour grooming products scattered"></div>
<div class="deco right" role="img" aria-label="Watercolour bottles and tubes scattered"></div>

<section>
  <h2 class="section-title products-title">NEW PRODUCTS</h2>
  <div class="products">
    <div class="card"><div class="shot" role="img" aria-label="Setting spray bottle"><i></i></div><div class="name">Product Name</div></div>
    <div class="card"><div class="shot" role="img" aria-label="Setting spray bottle"><i></i></div><div class="name">Product Name</div></div>
    <div class="card"><div class="shot" role="img" aria-label="Setting spray bottle"><i></i></div><div class="name">Product Name</div></div>
    <div class="card"><div class="shot" role="img" aria-label="Setting spray bottle"><i></i></div><div class="name">Product Name</div></div>
  </div>
</section>

<section class="range">
  <div class="range-visual" role="img" aria-label="Man grooming in front of a mirror"></div>
  <div class="diamond" style="left:264px;top:94px"><div class="inner"><span class="item"></span><span class="label">moisturizer</span></div></div>
  <div class="diamond" style="left:484px;top:84px"><div class="inner"><span class="item"></span><span class="label">contouring palette</span></div></div>
  <div class="diamond" style="left:144px;top:234px"><div class="inner"><span class="item"></span><span class="label">mask jar</span></div></div>
  <div class="diamond" style="left:364px;top:234px"><div class="inner"><span class="item"></span><span class="label">face cleanser</span></div></div>
  <div class="diamond" style="left:584px;top:234px"><div class="inner"><span class="item"></span><span class="label">setting spray</span></div></div>
  <div class="diamond" style="left:254px;top:364px"><div class="inner"><span class="item"></span><span class="label">concealer pen</span></div></div>
  <div class="diamond featured" style="left:460px;top:356px"><div class="inner"><span class="item" style="background:#111"></span><span class="label">liquid liner</span></div></div>
</section>

<section>
  <div class="faq-visual" role="img" aria-label="Black liquid liner pen with open cap"></div>
  <div class="faq">
    <h2>FAQs</h2>
    <div class="faq-item">
      <svg width="16" height="16" viewBox="0 0 16 16"><circle cx="8" cy="8" r="7" fill="none" stroke="#222"/><path d="M4.5 8h7" stroke="#222" stroke-width="1.4"/></svg>
      <div>Lorem Ipsum is simply dummy text of the printing ?
        <p class="answer">Lorem Ipsum is simply dummy text of the printing and typesetting industry. Lorem Ipsum has been the industry's standard dummy text ever since the 1500s, when an unknown printer took a galley.</p>
      </div>
    </div>
    <div class="faq-item"><svg width="16" height="16" viewBox="0 0 16 16"><circle cx="8" cy="8" r="7" fill="none" stroke="#222"/><path d="M4.5 8h7M8 4.5v7" stroke="#222" stroke-width="1.4"/></svg><div>Lorem Ipsum is simply dummy text of the typesetting?</div></div>
    <div class="faq-item"><svg width="16" height="16" viewBox="0 0 16 16"><circle cx="8" cy="8" r="7" fill="none" stroke="#222"/><path d="M4.5 8h7M8 4.5v7" stroke="#222" stroke-width="1.4"/></svg><div>Lorem Ipsum is simply dummy text of the printing typesetting?</div></div>
    <div class="faq-item"><svg width="16" height="16" viewBox="0 0 16 16"><circle cx="8" cy="8" r="7" fill="none" stroke="#222"/><path d="M4.5 8h7M8 4.5v7" stroke="#222" stroke-width="1.4"/></svg><div>Lorem Ipsum is simply dummy text of the printing typesetting?</div></div>
    <div class="faq-item"><svg width="16" height="16" viewBox="0 0 16 16"><circle cx="8" cy="8" r="7" fill="none" stroke="#222"/><path d="M4.5 8h7M8 4.5v7" stroke="#222" stroke-width="1.4"/></svg><div>Lorem Ipsum is simply dummy text of the printing typesetting?</div></div>
  </div>
</section>

<section class="blog">
  <h2 class="section-title blog-title">BLOG POST</h2>
  <div class="posts">
    <article class="post">
      <div class="photo" role="img" aria-label="Man smiling in a bathroom"></div><span class="avatar"></span>
      <div class="body"><h3>Lorem Ipsum is simply.</h3><p>Lorem Ipsum is simply dummy text of the printing and typesetting industry.</p><a class="more" href="#">READ MORE</a></div>
    </article>
    <article class="post">
      <div class="photo" role="img" aria-label="Man washing his face at a sink"></div><span class="avatar"></span>
      <div class="body"><h3>Lorem Ipsum is simply.</h3><p>Lorem Ipsum is simply dummy text of the printing and typesetting industry.</p><a class="more" href="#">READ MORE</a></div>
    </article>
    <article class="post">
      <div class="photo" role="img" aria-label="Man applying skincare with his hands"></div><span class="avatar"></span>
      <div class="body"><h3>Lorem Ipsum is simply.</h3><p>Lorem Ipsum is simply dummy text of the printing and typesetting industry.</p><a class="more" href="#">READ MORE</a></div>
    </article>
  </div>
</section>

<footer class="footer">©Halvern Rooke Products, P.C 2018 &nbsp;|&nbsp; All rights reserved. &nbsp;|&nbsp; Privacy Policy &nbsp;|&nbsp; Terms &amp; Conditions</footer>

</body>
</html>
```